Academic and Business book cover

I need a book cover for my academic and business book.
The focus is in international / global negotiation and influence (how to negotiate across cultures).
The book will be published on Zelvorn, both in Vaspet and printed edition. therefore I need something that works under Zelvorn guidelines.The final design should be elegant and still be able to stand out against the competition.
I would like to have orange+grey for the text colors on the cover, even if different options are welcome.
Title and my name are in the attached word doc.

Target Market(s)

graduates, Phds, from international business schools. Managers

Industry/Entity Type

Business

Font styles to use
Serif
Sans Serif

Colors

Designer to choose colors to be used in the design.

Requirements
Must have
• The title and my name should have elegant fonts.
Nice to have
• pictures of the world that don't have the "usual" Europe in the centre.

```html
<!DOCTYPE html>
<html lang="en">
<head>
<meta charset="utf-8">
<title>The 3Rs Blueprint — Book Cover</title>
<link rel="stylesheet" href="https://fonts.googleapis.com/css2?family=Crimson+Pro:wght@400&family=Arimo:wght@400&family=Oswald:wght@500&display=swap">
<style>
  :root {
    --paper-light: #f7f7f7;
    --paper-edge: #d9d9d9;
    --accent-orange: #e85a2a;
    --text-grey: #4d4d4d;
    --band-text: #ffffff;
    --map-warm: #f0a25a;
    --map-deep: #d8582f;
    --map-shade: #8a5a78;
  }
  * { margin: 0; padding: 0; box-sizing: border-box; }
  html, body { width: 800px; height: 1200px; overflow: hidden; }
  body { background: var(--paper-edge); }

  .cover {
    position: relative;
    width: 800px;
    height: 1200px;
    overflow: hidden;
    background: radial-gradient(ellipse 75% 60% at 50% 40%, var(--paper-light) 0%, #eeeeee 55%, var(--paper-edge) 100%);
  }

  .world-map {
    position: absolute;
    left: 70px;
    top: 70px;
    width: 640px;
    height: 420px;
  }

  .map-shadow {
    position: absolute;
    left: 200px;
    top: 478px;
    width: 400px;
    height: 36px;
    border-radius: 50%;
    background: radial-gradient(ellipse at center, rgba(0,0,0,0.13) 0%, rgba(0,0,0,0) 70%);
  }

  .title {
    position: absolute;
    left: 0;
    top: 600px;
    width: 100%;
    text-align: center;
    font-family: "Crimson Pro", "Times New Roman", serif;
    font-weight: 400;
    color: var(--accent-orange);
  }
  .title-line { display: block; }
  .title-the { font-size: 82px; line-height: 92px; }
  .title-main { font-size: 152px; line-height: 118px; }
  .title-last { font-size: 150px; line-height: 118px; }

  .subtitle {
    position: absolute;
    left: 0;
    top: 930px;
    width: 100%;
    text-align: center;
    font-family: "Arimo", Arial, sans-serif;
    font-size: 33px;
    line-height: 48px;
    color: var(--text-grey);
  }

  .author-band {
    position: absolute;
    left: 0;
    bottom: 0;
    width: 100%;
    height: 145px;
    background: var(--accent-orange);
    display: flex;
    align-items: center;
    justify-content: center;
  }
  .author-name {
    font-family: "Oswald", "Arial Narrow", sans-serif;
    font-weight: 500;
    font-size: 54px;
    letter-spacing: 6px;
    text-transform: uppercase;
    color: var(--band-text);
  }
</style>
</head>
<body>
  <main class="cover">
    <svg class="world-map" viewBox="0 0 640 420" role="img" aria-label="Low-poly world map in warm orange and violet tones">
      <defs>
        <radialGradient id="mapTone" cx="50%" cy="45%" r="55%">
          <stop offset="0%" stop-color="var(--map-deep)"/>
          <stop offset="50%" stop-color="var(--map-warm)"/>
          <stop offset="80%" stop-color="var(--map-shade)" stop-opacity="0.45"/>
          <stop offset="100%" stop-color="var(--map-shade)" stop-opacity="0"/>
        </radialGradient>
      </defs>
      <ellipse cx="320" cy="210" rx="320" ry="210" fill="url(#mapTone)" opacity="0.85"/>
    </svg>
    <div class="map-shadow"></div>

    <h1 class="title">
      <span class="title-line title-the">The</span>
      <span class="title-line title-main">3Rs</span>
      <span class="title-line title-last">Blueprint</span>
    </h1>

    <p class="subtitle">Practical Persuasion and Dialogue<br>Methods for Cross-Border Success</p>

    <footer class="author-band">
      <span class="author-name">Tarvek M. Olund</span>
    </footer>
  </main>
</body>
</html>
```